Business card design for new eCommerce site focusing on integrity and strong businsess tactics

We need a business card that will stand out and be memorable. Something with color that matches our company logo colors. Think high end version of Pactivo. There are 2 logos provided. The parent company is called Amber Ledge Partners and we are presenting a new and very exciting eCommerce site called BrightHarborTrade.example.

Target Market(s)

Our target markets are in the Activities, Food and Beverage, Health and Beauty

Industry/Entity Type

Marketing

Contact Information for Business Card

We have 4 members that need cards...I will provide all info to the winner of the design contest
Business Address is
4870 West 63rd Avenue, Suite C207
Phoenix AZ 85731

Font styles to use
Serif
Sans Serif

Colors

Designer to choose colors to be used in the design.

Requirements
Must have
• The card must be memorable...should be unique in design but must exude integrity and be playful .
• I have provided several colors or our parent company...please feel free to use which ever
Nice to have
• I will leave this up to you. Feel free to use other images of your choosing that wraps around our client.....Activities, Dining, Health, Beauty
Should not have
• just dont be boring

```html
<!DOCTYPE html>
<html lang="en">
<head>
<meta charset="utf-8">
<title>Business Cards – Amber Ledge Partners / BrightHarborTrade</title>
<link href="https://fonts.googleapis.com/css2?family=Montserrat:wght@500;700&family=Questrial&display=swap" rel="stylesheet">
<style>
  :root{
    --navy:#17234f;
    --green:#7dbb3c;
    --blue:#2a7fbf;
    --grey:#6b6b6b;
    --paper:#ffffff;
    --backdrop:#e4e4e4;
  }
  *{margin:0;padding:0;box-sizing:border-box}
  html,body{width:1200px;height:900px;overflow:hidden}
  body{background:var(--backdrop);position:relative;font-family:"Questrial",sans-serif}
  .card{position:absolute;left:300px;width:600px;height:343px;background:var(--paper);
    box-shadow:0 6px 18px rgba(0,0,0,.18)}
  .card--parent{top:60px}
  .card--site{top:480px}

  /* parent card */
  .parent-mark{position:absolute;left:50%;top:62px;transform:translateX(-50%);
    width:110px;height:110px;border-radius:50%;background:var(--navy);
    box-shadow:0 0 0 3px var(--paper),0 0 0 4px var(--navy)}
  .parent-name{position:absolute;top:192px;width:100%;text-align:center;
    font-family:"Montserrat",sans-serif;font-weight:700;font-size:30px;color:var(--navy)}
  .parent-web{position:absolute;bottom:34px;width:100%;text-align:center;
    font-family:"Montserrat",sans-serif;font-weight:500;font-size:13px;letter-spacing:1.5px;color:var(--navy)}

  /* site card */
  .brand{position:absolute;top:38px;left:88px;display:flex;align-items:center;gap:16px}
  .brand-mark{width:62px;height:62px;border-radius:50%;background:var(--green)}
  .brand-name{font-family:"Montserrat",sans-serif;font-weight:700;font-size:28px;color:var(--blue);line-height:1}
  .brand-tagline{font-size:14px;letter-spacing:2px;color:var(--grey);margin-top:6px}
  .person{position:absolute;top:168px;right:335px;text-align:right}
  .person-name{font-size:28px;line-height:1.1}
  .person-name .first{color:var(--green)}
  .person-name .last{color:var(--blue)}
  .person-role{font-size:19px;color:var(--grey);margin-top:2px}
  .divider{position:absolute;left:282px;top:172px;width:2px;height:64px;background:var(--blue)}
  .contact{position:absolute;left:302px;top:168px;list-style:none}
  .contact li{display:flex;align-items:center;gap:12px;font-size:16px;letter-spacing:1px;color:var(--grey);height:25px}
  .contact svg{width:14px;height:14px;fill:none;stroke:var(--blue);stroke-width:2}
  .address{position:absolute;bottom:30px;width:100%;text-align:center;font-size:16px;letter-spacing:1px;color:var(--grey)}
</style>
</head>
<body>
  <section class="card card--parent">
    <div class="parent-mark"></div>
    <div class="parent-name">Amber Ledge Partners</div>
    <div class="parent-web">www.amberledgepartners.example</div>
  </section>

  <section class="card card--site">
    <div class="brand">
      <div class="brand-mark"></div>
      <div>
        <div class="brand-name">BrightHarborTrade.example</div>
        <div class="brand-tagline">Activities-Dining-Health-Beauty</div>
      </div>
    </div>

    <div class="person">
      <div class="person-name"><span class="first">Daniel</span> <span class="last">Reyes</span></div>
      <div class="person-role">Founder</div>
    </div>
    <div class="divider"></div>
    <ul class="contact">
      <li><svg viewBox="0 0 14 14"><rect x="3.5" y="1" width="7" height="12" rx="1.5"/></svg>0400 555 019</li>
      <li><svg viewBox="0 0 14 14"><rect x="1" y="3" width="12" height="8" style="fill:var(--blue)"/><path d="M1 3l6 5 6-5" stroke="#fff"/></svg>info@brightharbortrade.example</li>
      <li><svg viewBox="0 0 14 14"><circle cx="6" cy="6" r="4"/><path d="M9 9l4 4"/></svg>www.brightharbortrade.example</li>
    </ul>
    <div class="address">4870 West 63rd Avenue, Suite C207 Phoenix AZ 85731</div>
  </section>
</body>
</html>
```